Logo and Card design for KRV Home Solutions LLC

I need an edgier logo and business card designs. Current logo attached. I like the colors below. I would like the logo to incorporate a home in the design.
Title = Principal-Acquisitions
Email:KRVHOMESOLUTIONS@fernmail.example
555-214-0937
facebook
IG
2 sided business card with the front being contact info a slogan about selling a home fast. The back incorporating What we do. Buy houses, land, or commercial property as is. We find solutions to make the process of selling simple and fair.

Target Market(s)

Motivated house sellers.

Industry/Entity Type

Business

Contact Information for Business Card

Who we are: We are a Faith based Real Estate Investment Company. We pay cash for homes in any condition and can close quick. Whatever the reason you need to sell fast, we can help. We believe in creating win-win solutions to help you in your time of need. We care! We can help!

Logo Text

KRV Home Solutions LLC

Font styles to use
Sans Serif

Colors
33a6d7
0355a3
85abd2
cee9f5
9d9d9d
b2b2b2
ffffff

Requirements
Must have
• Old logo attached. I want something edgier.
• Company name, phone number, description on the back of what we can do. Pay all cash. Buy in as is condition. No fees,Commisions or closing costs.Close quick. No hassles with solutions to meet your unique situation.
• Call today for an offer within 24 hours.

```html
<!DOCTYPE html>
<html lang="en">
<head>
<meta charset="utf-8">
<title>KRV Home Solutions – Business Card</title>
<link rel="stylesheet" href="https://fonts.googleapis.com/css2?family=Roboto:wght@400;500;700&family=Roboto+Condensed:wght@400;700&display=swap">
<style>
  :root {
    --backdrop: #2a2a2a;
    --navy: #1e3a6e;
    --navy-accent: #1f3b73;
    --slate: #5a5d62;
    --text-dark: #3d4045;
    --white: #ffffff;
    --photo-sky: #eef1f2;
    --photo-house: #dcdcd6;
    --photo-lawn: #d7e0c4;
  }
  * { margin: 0; padding: 0; box-sizing: border-box; }
  html, body {
    width: 1200px; height: 960px; overflow: hidden;
    background: var(--backdrop);
  }
  .canvas { position: relative; width: 1200px; height: 960px; }

  .card { position: absolute; width: 600px; height: 343px; overflow: hidden; }

  /* Front */
  .card-front { left: 314px; top: 113px; }
  .card-front .house-photo {
    position: absolute; inset: 0;
    background: linear-gradient(180deg, var(--photo-sky) 0%, var(--photo-house) 45%, #e4e6e0 70%, var(--photo-lawn) 100%);
  }
  .name-accent {
    position: absolute; left: 0; top: 106px; width: 15px; height: 44px;
    background: var(--navy-accent);
  }
  .holder-name {
    position: absolute; left: 36px; top: 110px;
    font: 700 23px/1 "Roboto Condensed", sans-serif;
    color: var(--navy-accent); letter-spacing: 0.2px;
  }
  .holder-title {
    position: absolute; left: 36px; top: 137px;
    font: 500 15px/1 "Roboto", sans-serif; color: var(--slate);
  }
  .benefits {
    position: absolute; left: 28px; top: 216px; list-style: none;
    font: 400 15px/18px "Roboto Condensed", sans-serif; color: var(--text-dark);
  }
  .benefits li { position: relative; padding-left: 14px; }
  .benefits li::before {
    content: ""; position: absolute; left: 2px; top: 7px;
    width: 5px; height: 5px; border-radius: 50%; background: var(--navy-accent);
  }
  .brand-name {
    position: absolute; left: 318px; top: 112px; width: 204px;
    display: flex; align-items: center; gap: 10px;
    font: 700 26px/1.05 "Roboto", sans-serif; color: var(--navy-accent);
  }
  .brand-name .brand-square {
    flex: none; width: 18px; height: 18px; background: var(--slate);
  }
  .contact {
    position: absolute; left: 300px; top: 248px; list-style: none;
    font: 400 14px/19.5px "Roboto", sans-serif; color: var(--text-dark);
    white-space: nowrap;
  }
  .contact li { display: flex; align-items: center; gap: 8px; }
  .contact svg { width: 14px; height: 14px; fill: var(--navy-accent); flex: none; }

  /* Back */
  .card-back {
    left: 311px; top: 472px; background: var(--navy);
    color: var(--white); text-align: center; font-family: "Roboto", sans-serif;
  }
  .back-brand {
    position: absolute; left: 0; right: 0; top: 94px;
    font: 700 30px/1 "Roboto", sans-serif; letter-spacing: 1px;
  }
  .back-rule {
    position: absolute; left: 102px; top: 137px; width: 390px; height: 2px;
    background: var(--white);
  }
  .section-heading { font-weight: 700; font-size: 15px; line-height: 18px; margin-bottom: 3px; }
  .section-body { font-weight: 400; font-size: 15.2px; line-height: 18px; }
  .who-we-are { position: absolute; left: 0; right: 0; top: 157px; }
  .what-we-do { position: absolute; left: 0; right: 0; top: 243px; }
</style>
</head>
<body>
<div class="canvas">

  <section class="card card-front">
    <div class="house-photo" role="img" aria-label="Faded photograph of a two-storey suburban house with front porch and lawn"></div>
    <div class="name-accent"></div>
    <h1 class="holder-name">MARCUS REED</h1>
    <p class="holder-title">Principal-Acquisitions</p>
    <ul class="benefits">
      <li>Pay all cash. Buy in as is condition</li>
      <li>No fees,Commisions or closing costs</li>
      <li>Close quick. No hassles with<br>solutions to meet your unique situation</li>
      <li>Call today for an offer within 24 hours</li>
    </ul>
    <div class="brand-name"><span class="brand-square"></span><span>KRV HOME SOLUTIONS</span></div>
    <ul class="contact">
      <li><svg viewBox="0 0 24 24" aria-hidden="true"><path d="M6.6 10.8a15.1 15.1 0 0 0 6.6 6.6l2.2-2.2a1 1 0 0 1 1-.25 11.4 11.4 0 0 0 3.6.57 1 1 0 0 1 1 1V20a1 1 0 0 1-1 1A17 17 0 0 1 3 4a1 1 0 0 1 1-1h3.5a1 1 0 0 1 1 1c0 1.25.2 2.45.57 3.57a1 1 0 0 1-.25 1z"/></svg>555-214-0937</li>
      <li><svg viewBox="0 0 24 24" aria-hidden="true"><path d="M2 5h20v2l-10 6L2 7z M2 9l10 6 10-6v10H2z"/></svg>KRVHOMESOLUTIONS@fernmail.example</li>
      <li><svg viewBox="0 0 24 24" aria-hidden="true"><path d="M12 2a10 10 0 1 0 0 20 10 10 0 0 0 0-20zm-1 17.9A8 8 0 0 1 4.2 10.5L9 15.3v1a2 2 0 0 0 2 2zm6.9-2.5a2 2 0 0 0-1.9-1.4h-1v-3a1 1 0 0 0-1-1H8v-2h2a1 1 0 0 0 1-1V7h2a2 2 0 0 0 2-2v-.4a8 8 0 0 1 2.9 12.8z"/></svg>KRVHOMESOLUTIONS.example</li>
    </ul>
  </section>

  <section class="card card-back">
    <div class="back-brand">KRV HOME SOLUTIONS</div>
    <div class="back-rule"></div>
    <div class="who-we-are">
      <h2 class="section-heading">WHO WE ARE</h2>
      <p class="section-body">We are a Faith based Real Estate Investment Company. We pay cash for<br>homes in any condition and can close quick. Whatever the reason you need<br>to sell fast, we can help. We believe in creating win-win solutions to help</p>
    </div>
    <div class="what-we-do">
      <h2 class="section-heading">WHAT WE DO</h2>
      <p class="section-body">Buy houses, land, or commercial property as is.<br>We find solutions to make the process of selling simple and fair.</p>
    </div>
  </section>

</div>
</body>
</html>
```